Business card design needed

I need a business card for my private practice. I would like to see the designs that use bright blue and white. I would like to see similar designs as to the card below:
http://blog.cardnookprint.com/2009/designing-a-business-card-with-cn-rx518-template.html
I would like to see the back of the card have room for appointment times. Thank you.

Industry/Entity Type
Business
Contact Information for Business Card
Harbourline Wellbeing & Guidance Services
Megan Trawley B.Psychology
Registered Psychologist
Unit C, Floor 3, 42 Mortlake Parade, Canberra, ACT 2602
T: (02) 6283 7715
F: (02) 6283 7790
info@harbourlinewellbeing.com.au
www.harbourlinewellbeing.com.au

```html
<!DOCTYPE html>
<html lang="en">
<head>
<meta charset="utf-8">
<title>Harbourline Wellbeing &amp; Guidance Services — Business Card</title>
<link rel="stylesheet" href="https://fonts.googleapis.com/css2?family=Jost:ital,wght@0,400;0,500;1,500;1,600&display=swap">
<style>
  :root {
    --stage: #eef1f4;
    --blue-light: #35c8f7;
    --blue-deep: #05aef0;
    --blue-ink: #1cb6f2;
    --white: #ffffff;
    --paper: #f7f7f7;
    --shadow: rgba(20, 40, 60, 0.18);
  }
  * { box-sizing: border-box; margin: 0; padding: 0; }
  html, body {
    width: 1200px; height: 675px; overflow: hidden;
    background: var(--stage);
    font-family: "Jost", "Futura", sans-serif;
  }
  .stage {
    position: relative; width: 1200px; height: 675px;
    display: flex; align-items: center; justify-content: center; gap: 60px;
  }
  .card {
    position: relative; width: 510px; height: 292px;
    box-shadow: 0 10px 26px var(--shadow);
    overflow: hidden;
  }

  /* Front */
  .card-front {
    background: linear-gradient(160deg, var(--blue-light) 0%, var(--blue-deep) 100%);
    color: var(--white);
  }
  .front-brand {
    position: absolute; top: 44px; right: 34px; text-align: right;
  }
  .brand-name {
    font-style: italic; font-weight: 600; font-size: 15.5px; letter-spacing: 0.2px;
  }
  .brand-url {
    font-style: italic; font-weight: 500; font-size: 11.5px; margin-top: 1px; letter-spacing: 0.3px;
  }
  .person {
    position: absolute; top: 128px; left: 70px; text-align: right; width: 180px;
  }
  .person-name { font-weight: 500; font-size: 25px; line-height: 1.1; }
  .person-title { font-style: italic; font-weight: 500; font-size: 9.5px; margin-top: 3px; opacity: 0.92; }
  .divider {
    position: absolute; left: 266px; top: 128px; width: 1px; height: 70px;
    background: var(--white); opacity: 0.85;
  }
  .contact-list {
    position: absolute; left: 280px; top: 126px; list-style: none;
    font-size: 10.5px; line-height: 1.25; font-weight: 500;
  }
  .contact-list li { display: flex; align-items: flex-start; gap: 7px; margin-bottom: 2px; }
  .contact-list svg { width: 10px; height: 10px; flex: none; margin-top: 2px; }

  /* Back */
  .card-back { background: var(--paper); color: var(--blue-ink); }
  .appointment {
    position: absolute; top: 40px; right: 40px; width: 170px;
    border-bottom: 1.5px solid var(--blue-ink); padding: 0 0 4px 22px;
    font-size: 17px; font-weight: 400;
  }
  .back-brand { position: absolute; top: 140px; left: 52px; }
  .back-brand .brand-name { font-size: 14px; }
  .back-brand .brand-url { font-size: 9px; padding-left: 60px; }
</style>
</head>
<body>
<main class="stage">
  <section class="card card-front" aria-label="Business card front">
    <header class="front-brand">
      <p class="brand-name">Harbourline Wellbeing &amp; Guidance Services</p>
      <p class="brand-url">www.harbourlinewellbeing.com.au</p>
    </header>
    <div class="person">
      <h1 class="person-name">Megan Trawley</h1>
      <p class="person-title">B.Psychology Registered Psychologist</p>
    </div>
    <div class="divider"></div>
    <ul class="contact-list">
      <li>
        <svg viewBox="0 0 10 10" aria-hidden="true"><path d="M5 0.5a3 3 0 0 1 3 3c0 2.2-3 6-3 6s-3-3.8-3-6a3 3 0 0 1 3-3z" fill="none" stroke="currentColor" stroke-width="1.1"/><circle cx="5" cy="3.5" r="1" fill="currentColor"/></svg>
        <span>Unit C, Floor 3, 42 Mortlake Parade,<br>Canberra, ACT 2602</span>
      </li>
      <li>
        <svg viewBox="0 0 10 10" aria-hidden="true"><circle cx="5" cy="5" r="4.3" fill="none" stroke="currentColor" stroke-width="1"/><path d="M3.4 3c.3 1.8 1.5 3.3 3.3 3.9l.6-.8-.9-.6-.5.4c-.6-.3-1.1-.9-1.4-1.5l.4-.5-.6-.9z" fill="currentColor"/></svg>
        <span>(02) 6283 7715</span>
      </li>
      <li>
        <svg viewBox="0 0 10 10" aria-hidden="true"><rect x="1" y="4" width="8" height="5" rx="0.8" fill="none" stroke="currentColor" stroke-width="1"/><rect x="2.6" y="1" width="4.8" height="3" fill="none" stroke="currentColor" stroke-width="1"/></svg>
        <span>(02) 6283 7790</span>
      </li>
      <li>
        <svg viewBox="0 0 10 10" aria-hidden="true"><rect x="0.8" y="2" width="8.4" height="6" fill="none" stroke="currentColor" stroke-width="1"/><path d="M0.8 2l4.2 3.3 4.2-3.3" fill="none" stroke="currentColor" stroke-width="1"/></svg>
        <span>info@harbourlinewellbeing.com.au</span>
      </li>
    </ul>
  </section>

  <section class="card card-back" aria-label="Business card back">
    <h2 class="appointment">Appointment</h2>
    <div class="back-brand">
      <p class="brand-name">Harbourline Wellbeing &amp; Guidance Services</p>
      <p class="brand-url">www.harbourlinewellbeing.com.au</p>
    </div>
  </section>
</main>
</body>
</html>
```